BOLD & MINIMALIST DESIGN NEEDED

We want a very bold but minimalistic business card design that is impactful and utilizes both sides of the business card. Our current logo is included for your use.

We want bold fonts and good use of negative space. We don't want the logo to overpower the design.

Target Market(s)

Professionals who are building new commercial buildings.

Industry/Entity Type

Construction

Contact Information for Business Card

Name, Title, email, office phone, cell phone, website

Font styles to use
Serif
Sans Serif

Requirements
Must have
• Bold design!

```html
<!DOCTYPE html>
<html lang="en">
<head>
<meta charset="utf-8">
<title>Summitcrest Business Card</title>
<link rel="stylesheet" href="https://fonts.googleapis.com/css2?family=Roboto+Condensed:wght@700&family=Libre+Baskerville&family=Noto+Sans:wght@400&display=swap">
<style>
  :root {
    --backdrop: #00676a;
    --card: #ffffff;
    --ink-dark: #0d2b33;
    --gold: #dcb42a;
    --teal: #0d6d6d;
    --navy: #1a1a3a;
    --black: #111111;
  }
  html, body {
    margin: 0;
    padding: 0;
    width: 1200px;
    height: 1200px;
    overflow: hidden;
    background: var(--backdrop);
  }
  .canvas { display: block; width: 1200px; height: 1200px; }
  .card-base { fill: var(--card); }
  .shape-dark { fill: var(--ink-dark); }
  .shape-gold { fill: var(--gold); }
  .band-dark { stroke: var(--ink-dark); stroke-width: 58; stroke-linecap: butt; }
  .band-thin { stroke: var(--ink-dark); stroke-width: 14; }
  .brand-name {
    font-family: "Roboto Condensed", "Arial Narrow", sans-serif;
    font-weight: 700;
    font-size: 84px;
    fill: var(--black);
    letter-spacing: 1px;
  }
  .web-icon { fill: none; stroke: var(--teal); stroke-width: 7; }
  .website {
    font-family: "Libre Baskerville", Georgia, serif;
    font-size: 34px;
    fill: var(--navy);
  }
  .person-name {
    font-family: "Roboto Condensed", "Arial Narrow", sans-serif;
    font-weight: 700;
    font-size: 64px;
    fill: var(--teal);
  }
  .person-title {
    font-family: "Libre Baskerville", Georgia, serif;
    font-size: 34px;
    fill: var(--black);
  }
  .divider { fill: var(--black); }
  .contact-icon { fill: none; stroke: var(--black); stroke-width: 5; stroke-linecap: round; stroke-linejoin: round; }
  .contact-phone {
    font-family: "Noto Sans", Arial, sans-serif;
    font-size: 34px;
    letter-spacing: 3px;
    fill: var(--black);
  }
  .contact-text {
    font-family: "Libre Baskerville", Georgia, serif;
    font-size: 32px;
    fill: var(--black);
  }
</style>
</head>
<body>
<svg class="canvas" viewBox="0 0 1932 1932" xmlns="http://www.w3.org/2000/svg">
  <defs>
    <clipPath id="card-clip">
      <rect x="189" y="114" width="1440" height="823"/>
    </clipPath>
    <g id="card-artwork">
      <rect class="card-base" x="189" y="114" width="1440" height="823"/>
      <g clip-path="url(#card-clip)">
        <polygon class="shape-gold" points="189,114 189,840 552,477"/>
        <line class="band-dark" x1="210" y1="90" x2="1090" y2="960"/>
        <line class="band-thin" x1="189" y1="905" x2="600" y2="494"/>
        <polygon class="shape-dark" points="1180,937 1629,640 1629,937"/>
      </g>
    </g>
  </defs>

  <g class="card-front">
    <use href="#card-artwork"/>
    <text class="brand-name" x="1183" y="532" text-anchor="middle">SUMMITCREST</text>
    <g class="web-icon">
      <circle cx="1194" cy="632" r="36"/>
      <ellipse cx="1194" cy="632" rx="15" ry="36"/>
      <line x1="1158" y1="632" x2="1230" y2="632"/>
    </g>
    <text class="website" x="1185" y="707" text-anchor="middle">www.yourmail.com</text>
  </g>

  <g class="card-back">
    <use href="#card-artwork" transform="translate(1818,896) scale(-1,1)"/>
    <text class="person-name" x="397" y="1140">Your Name</text>
    <text class="person-title" x="397" y="1188">Designation Here</text>
    <path class="divider" d="M300,1223 Q583,1213 866,1223 Q583,1233 300,1223 Z"/>

    <g class="contact-icon">
      <rect x="403" y="1336" width="30" height="44" rx="5"/>
      <line x1="414" y1="1370" x2="422" y2="1370"/>
    </g>
    <text class="contact-phone" x="466" y="1369">+123456789</text>

    <g class="contact-icon">
      <rect x="398" y="1434" width="40" height="30" rx="5"/>
      <polyline points="400,1438 418,1452 436,1438"/>
    </g>
    <text class="contact-text" x="462" y="1460">yourgmail@gmail.com</text>

    <g class="contact-icon">
      <path d="M416,1556 C402,1540 398,1532 398,1524 A18,18 0 0 1 434,1524 C434,1532 430,1540 416,1556 Z"/>
      <circle cx="416" cy="1524" r="6"/>
    </g>
    <text class="contact-text" x="459" y="1547">Your Address</text>
  </g>
</svg>
</body>
</html>
```